Animal Eye Clinic needs a Business card

We are a new veterinary ophthalmology practice (Ridgeline Pet Vision Care) and we need a business card designed. We only see animal eyes - we are not a regular veterinary clinic. We already have a logo. We are looking for a professional, good looking business card to hand out to our clients. We are looking for something simple but professional and contemporary. Our logo is likely the only picture/graphic that needs to be on the card.
Updates

Contact Information for Business Card

Delia Vossman, BSc, DVM, MSc, DipACVO
Veterinary Ophthalmologist

Phone: 250.418.3927
Email: ridgelinepetvisioncare@mailbox-example.net
Website: ridgelinepetvisioncare-example.net
Address: 1874 Thornbury Rd
Kelowna, BC, V1X 4M9

Colors

Designer to choose colors to be used in the design.

Requirements
Must have
• Our logo (attached)

```html
<!DOCTYPE html>
<html lang="en">
<head>
<meta charset="utf-8">
<title>Ridgeline Pet Vision Care – Business Card</title>
<link rel="stylesheet" href="https://fonts.googleapis.com/css2?family=Roboto:wght@400;500;700&display=swap">
<style>
  :root {
    --teal: #1b98a8;
    --teal-dark: #177f8c;
    --grey-text: #6d6d6d;
    --grey-mid: #7a7a7a;
    --rule: #9a9a9a;
    --card-white: #ffffff;
    --backdrop: #dfe2e5;
  }
  * { box-sizing: border-box; margin: 0; padding: 0; }
  html, body {
    width: 1200px; height: 800px; overflow: hidden;
    background: var(--backdrop);
    font-family: "Roboto", Arial, sans-serif;
  }
  .sheet {
    width: 1200px; height: 800px;
    display: flex; align-items: center; justify-content: center; gap: 40px;
  }
  .card {
    width: 560px; height: 320px;
    position: relative; overflow: hidden;
    box-shadow: 0 4px 14px rgba(0,0,0,0.18);
  }

  /* Back of card */
  .card--back { background: var(--teal); }
  .back-brand {
    position: absolute; left: 40px; top: 86px;
    color: var(--card-white); font-weight: 500; font-size: 26px;
    letter-spacing: 0.5px;
  }
  .back-web {
    position: absolute; left: 40px; top: 212px;
    color: var(--card-white); font-size: 13px; letter-spacing: 2.4px;
  }
  .back-art {
    position: absolute; right: 0; bottom: 0; width: 300px; height: 320px;
  }

  /* Front of card */
  .card--front { background: var(--card-white); }
  .front-brand {
    position: absolute; left: 36px; top: 34px;
    display: flex; align-items: center; gap: 12px;
  }
  .brand-dot {
    width: 38px; height: 38px; border-radius: 50%;
    background: var(--teal);
  }
  .brand-name {
    color: var(--teal); font-weight: 500; font-size: 22px; letter-spacing: 0.3px;
  }
  .person {
    position: absolute; left: 36px; top: 116px;
  }
  .person-name {
    color: var(--teal); font-weight: 700; font-size: 21px; text-transform: uppercase;
  }
  .person-credentials {
    font-size: 13px; font-weight: 700; margin-left: 4px; text-transform: none;
  }
  .person-title {
    color: var(--grey-text); font-size: 15px; margin-top: 2px;
  }
  .divider {
    position: absolute; left: 36px; right: 36px; top: 174px;
    border-top: 1px solid var(--rule);
  }
  .contact {
    position: absolute; left: 36px; top: 186px; list-style: none;
    color: var(--grey-text); font-size: 13.5px; line-height: 21px;
  }
  .contact li { display: flex; align-items: center; gap: 8px; }
  .contact svg { width: 12px; height: 12px; flex: none; }
  .address {
    position: absolute; right: 36px; bottom: 28px; text-align: right;
    color: var(--grey-text); font-size: 15px; line-height: 20px;
  }
</style>
</head>
<body>
<main class="sheet">

  <section class="card card--back">
    <p class="back-brand">Ridgeline Pet Vision Care</p>
    <p class="back-web">ridgelinepetvisioncare-example.net</p>
    <svg class="back-art" viewBox="0 0 300 320" role="img" aria-label="Silhouette illustration of a horse, a dog and a cat in profile">
      <defs>
        <linearGradient id="artTone" x1="0" y1="0" x2="1" y2="1">
          <stop offset="0" stop-color="#ffffff"/>
          <stop offset="0.55" stop-color="#e6f3f5"/>
          <stop offset="1" stop-color="#c9cccd"/>
        </linearGradient>
      </defs>
      <path d="M300 60 C230 70 160 120 110 190 C80 235 40 280 20 320 L300 320 Z" fill="url(#artTone)"/>
    </svg>
  </section>

  <section class="card card--front">
    <div class="front-brand">
      <span class="brand-dot"></span>
      <span class="brand-name">Ridgeline Pet Vision Care</span>
    </div>

    <div class="person">
      <p class="person-name">Delia Vossman<span class="person-credentials">BSc, DVM, MSc, DipACVO</span></p>
      <p class="person-title">Veterinary Ophthalmologist</p>
    </div>

    <div class="divider"></div>

    <ul class="contact">
      <li>
        <svg viewBox="0 0 12 12"><path d="M2.5 1 L4.5 1 L5.2 3.4 L4 4.4 C4.7 5.9 6 7.2 7.6 8 L8.6 6.8 L11 7.5 L11 9.5 C11 10.3 10.3 11 9.5 11 C5 11 1 7 1 2.5 C1 1.7 1.7 1 2.5 1Z" fill="var(--teal)"/></svg>
        250.418.3927
      </li>
      <li>
        <svg viewBox="0 0 12 12"><rect x="0.75" y="2.25" width="10.5" height="7.5" fill="none" stroke="var(--teal)" stroke-width="1.3"/><path d="M1 2.5 L6 6.5 L11 2.5" fill="none" stroke="var(--teal)" stroke-width="1.3"/></svg>
        ridgelinepetvisioncare@mailbox-example.net
      </li>
      <li>
        <svg viewBox="0 0 12 12"><circle cx="6" cy="6" r="5.2" fill="none" stroke="var(--teal)" stroke-width="1.1"/><ellipse cx="6" cy="6" rx="2.3" ry="5.2" fill="none" stroke="var(--teal)" stroke-width="1"/><path d="M1 6 H11 M1.8 3.5 H10.2 M1.8 8.5 H10.2" stroke="var(--teal)" stroke-width="0.9"/></svg>
        ridgelinepetvisioncare-example.net
      </li>
    </ul>

    <address class="address" style="font-style:normal">
      1874 Thornbury Rd<br>
      Kelowna, BC, V1X 4M9
    </address>
  </section>

</main>
</body>
</html>
```